Thornvale Group needs a business card design

We need a new business card design using the logo recently selected in a logo competition on Pixel Bazaar. Our business is a consultancy specializing in aviation and energy and the winning business card design will promote an image of precision and professionalism with creativity.

Please use the logo with the name on the front of the card and use a complementary font. Make the back white with either the light grey or dark grey logo.

Target Market(s)

Senior finance and legal leaders at aviation and energy companies

Industry/Entity Type

Management Consulting

Contact Information for Business Card

Peter Castrell
President
Thornvale Group

www.thornvalegroup.example

(555) 204-6391
pc@thornvalegroup.example

Requirements
Must have
• Professional font that goes well with the logo font

```html
<!DOCTYPE html>
<html lang="en">
<head>
<meta charset="utf-8">
<title>Thornvale Group – Business Card</title>
<link rel="stylesheet" href="https://fonts.googleapis.com/css2?family=Montserrat:wght@300&family=Open+Sans:wght@400;600&display=swap">
<style>
  :root {
    --navy: #123f6e;
    --white: #ffffff;
    --ink: #333a44;
    --backdrop: #e9eaec;
  }
  * { margin: 0; padding: 0; box-sizing: border-box; }
  html, body { width: 1200px; height: 900px; overflow: hidden; }
  body { position: relative; background: var(--backdrop); font-family: "Open Sans", sans-serif; }

  .card { position: absolute; border-radius: 16px; overflow: hidden; box-shadow: 0 6px 18px rgba(0,0,0,.12); }
  .card--front { left: 78px; top: 35px; width: 587px; height: 363px; background: var(--white); }
  .card--back  { left: 390px; top: 506px; width: 565px; height: 350px; background: var(--navy); }

  .band { position: absolute; }
  .card--front .band { background: var(--navy); top: 31px; height: 99px; }
  .card--front .band--left  { left: 0; width: 207px; }
  .card--front .band--right { left: 400px; right: 0; }
  .card--back .band { background: var(--white); top: 66px; height: 95px; }
  .card--back .band--left  { left: 0; width: 183px; }
  .card--back .band--right { left: 375px; right: 0; }

  .wordmark { position: absolute; left: 0; right: 0; text-align: center; font-family: "Montserrat", sans-serif; font-weight: 300; }
  .wordmark__name  { display: block; font-size: 38px; letter-spacing: 1px; line-height: 1; }
  .wordmark__group { display: block; font-size: 18px; letter-spacing: 17px; padding-left: 17px; line-height: 1; margin-top: 17px; }
  .card--front .wordmark { top: 172px; color: var(--navy); }
  .card--back .wordmark  { top: 207px; color: var(--white); }

  .person { position: absolute; right: 345px; top: 280px; text-align: right; }
  .person__name { font-size: 20px; font-weight: 600; color: var(--navy); line-height: 1.2; }
  .person__title { font-size: 15px; color: var(--ink); margin-top: 4px; }

  .contact { position: absolute; left: 281px; top: 282px; list-style: none; font-size: 15px; color: var(--ink); }
  .contact li { display: flex; align-items: center; height: 25px; }
  .contact svg { width: 12px; height: 12px; margin-right: 10px; fill: var(--navy); }
</style>
</head>
<body>
  <section class="card card--front" aria-label="Card front">
    <div class="band band--left"></div>
    <div class="band band--right"></div>
    <div class="wordmark">
      <span class="wordmark__name">THORNVALE</span>
      <span class="wordmark__group">GROUP</span>
    </div>
    <div class="person">
      <p class="person__name">Peter Castrell</p>
      <p class="person__title">President</p>
    </div>
    <ul class="contact">
      <li>
        <svg viewBox="0 0 24 24" aria-hidden="true"><path d="M6.6 10.8a15.1 15.1 0 0 0 6.6 6.6l2.2-2.2a1 1 0 0 1 1-.25 11.4 11.4 0 0 0 3.6.57 1 1 0 0 1 1 1V20a1 1 0 0 1-1 1A17 17 0 0 1 3 4a1 1 0 0 1 1-1h3.5a1 1 0 0 1 1 1c0 1.25.2 2.45.57 3.57a1 1 0 0 1-.25 1z"/></svg>
        (555) 204-6391
      </li>
      <li>
        <svg viewBox="0 0 24 24" aria-hidden="true"><path d="M2 5h20v14H2z M3.5 6.5 12 13l8.5-6.5" fill="var(--navy)" stroke="#fff" stroke-width="1.6"/></svg>
        pc@thornvalegroup.example
      </li>
    </ul>
  </section>

  <section class="card card--back" aria-label="Card back">
    <div class="band band--left"></div>
    <div class="band band--right"></div>
    <div class="wordmark">
      <span class="wordmark__name">THORNVALE</span>
      <span class="wordmark__group">GROUP</span>
    </div>
  </section>
</body>
</html>
```